Business Card Design Project : Ridgeline Press

In preparation for market launch, Tamarind's Ridgeline Press require the development of a business card. Ridgeline Press is a Community online publishing web portal. We provide the the city of Whistler located in B.C. (Canada) business directories, News, Classified ads, News, Events and blogs etc.

The main focus of the brand is to help local businesses to corporate with their online advertisement and marketing. Meeting our clients face to face is a must (B2B).

Target Market(s)

The target market is B2B customers. Business Owners to Marketing, advertising Managers

Industry/Entity Type

Business

Requirements
Must have
• - The business card will be two sided.
the BACK side will have our logo which consist of (icon, url,slogan) submited. The logo will be middle and centred.

The FRONT side should have company details:

Company Legal Name: TAMARIND RIDGELINE MEDIA

Owen Farsk
Director of Sales & Marketing

www.tamarindridgeline.biz
owen@tamarindridgeline.biz

Phone: 604 317 8842
#2714 - 582 E. Halvern St.
Vancouver, B.C. V7K2R4 Canada
Nice to have
• - For the "FRONT" side of our business card. You can separate or re-arrange with our logo components (icon, logo,slogan). It does not have to be together.

Also our company legal name is rather long so arrange or organize the name in a way to make it shorter. Your experience and creativity will have to come in play.
Should not have
• should not have other colors beside logo color and black text (2 colors). Also nothing Three dimensional

```html
<!DOCTYPE html>
<html lang="en">
<head>
<meta charset="utf-8">
<title>Ridgeline Press — Business Card</title>
<link rel="stylesheet" href="https://fonts.googleapis.com/css2?family=Open+Sans:wght@400;600;700;800&display=swap">
<style>
  :root {
    --brand-blue: #1b78c4;
    --brand-blue-deep: #0e5a9f;
    --ink: #1a1a1a;
    --paper: #ffffff;
    --backdrop: #e4e6e9;
  }
  * { margin: 0; padding: 0; box-sizing: border-box; }
  html, body { width: 1200px; height: 944px; overflow: hidden; }
  body {
    background: var(--backdrop);
    font-family: "Open Sans", Arial, sans-serif;
    position: relative;
  }
  .card {
    position: absolute;
    width: 600px;
    height: 343px;
    border-radius: 22px;
    overflow: hidden;
  }

  /* Back side */
  .card-back {
    left: 70px; top: 80px;
    background: linear-gradient(180deg, var(--brand-blue) 0%, var(--brand-blue-deep) 100%);
  }
  .back-brand {
    position: absolute;
    left: 0; right: 0; top: 72px;
    display: flex; align-items: center; justify-content: center; gap: 16px;
    color: var(--paper);
    font-weight: 700;
    font-size: 46px;
  }
  .brand-dot {
    width: 26px; height: 26px; border-radius: 50%;
    background: var(--paper);
  }
  .back-url {
    position: absolute;
    left: 70px; top: 176px;
    color: var(--ink);
    font-weight: 800;
    font-size: 37px;
    letter-spacing: -0.3px;
  }
  .back-slogan {
    position: absolute;
    left: 178px; top: 226px;
    color: var(--paper);
    font-size: 30px;
  }

  /* Front side */
  .card-front {
    left: 530px; top: 500px;
    background: var(--paper);
  }
  .front-shape { position: absolute; inset: 0; }
  .front-brand {
    position: absolute;
    left: 58px; top: 46px;
    display: flex; align-items: center; gap: 10px;
    color: var(--brand-blue);
    font-weight: 700;
    font-size: 28px;
  }
  .front-brand .brand-dot { width: 16px; height: 16px; background: var(--brand-blue); }
  .front-slogan {
    position: absolute;
    left: 84px; top: 94px;
    color: var(--brand-blue);
    font-size: 17px;
  }
  .contact-list {
    position: absolute;
    left: 52px; top: 148px;
    list-style: none;
    color: var(--ink);
    font-size: 15px;
    line-height: 20px;
  }
  .contact-list li { display: flex; align-items: flex-start; gap: 8px; margin-bottom: 4px; }
  .contact-list .icon { width: 14px; height: 14px; flex: none; margin-top: 3px; fill: var(--brand-blue-deep); }
  .contact-address { margin-bottom: 14px !important; }
  .person {
    position: absolute;
    right: 30px; top: 262px;
    text-align: center;
    color: var(--paper);
  }
  .person-name { font-size: 22px; font-weight: 400; }
  .person-title { font-size: 15px; }
</style>
</head>
<body>

<section class="card card-back" aria-label="Business card, back side">
  <div class="back-brand"><span class="brand-dot"></span>Ridgeline Press</div>
  <div class="back-url">www.tamarindridgeline.biz</div>
  <div class="back-slogan">Your information gateway</div>
</section>

<section class="card card-front" aria-label="Business card, front side">
  <svg class="front-shape" width="600" height="343" viewBox="0 0 600 343">
    <path d="M392 0 C350 110 328 230 300 343 L600 343 L600 0 Z" fill="var(--brand-blue)"/>
    <path d="M368 0 C322 110 296 230 262 343 L300 343 C328 230 350 110 392 0 Z" fill="var(--ink)"/>
  </svg>

  <div class="front-brand"><span class="brand-dot"></span>Ridgeline Press</div>
  <div class="front-slogan">Your information gateway</div>

  <ul class="contact-list">
    <li class="contact-address">
      <svg class="icon" viewBox="0 0 14 14"><path d="M7 1 L13 7 H11 V13 H8.5 V9 H5.5 V13 H3 V7 H1 Z"/></svg>
      <span>#2714 - 582 E. Halvern St.<br>Vancouver, B.C. V7K2R4 Canada</span>
    </li>
    <li>
      <svg class="icon" viewBox="0 0 14 14"><path d="M3 1 L5.5 1 L6.5 4 L5 5.5 C5.8 7.3 6.7 8.2 8.5 9 L10 7.5 L13 8.5 L13 11 C13 12 12 13 11 13 C5.5 12.5 1.5 8.5 1 3 C1 2 2 1 3 1 Z"/></svg>
      <span>604 317 8842</span>
    </li>
    <li>
      <svg class="icon" viewBox="0 0 14 14"><path d="M1 3 H13 V11 H1 Z M1.8 3.8 L7 8 L12.2 3.8" fill="var(--brand-blue-deep)"/><path d="M1.8 3.8 L7 8 L12.2 3.8" fill="none" stroke="#fff" stroke-width="1"/></svg>
      <span>owen@tamarindridgeline.biz</span>
    </li>
    <li>
      <svg class="icon" viewBox="0 0 14 14"><circle cx="7" cy="7" r="6.5"/></svg>
      <span>www.tamarindridgeline.biz</span>
    </li>
  </ul>

  <div class="person">
    <div class="person-name">Owen Farsk</div>
    <div class="person-title">Director of Sales &amp; Marketing</div>
  </div>
</section>

</body>
</html>
```